Construction company stationary design

We're wanting to develop a new professional stationary set for a newly establised property related business using our existing logo (attached). Business incorporates renovations, property investment and property development.

Specifically needing letter head, business cards, envelopes, email signature and need to get tshirt and caps embroydered.

Looking for something quite modern but professional using white, black and green.

Investment

```html
<!DOCTYPE html>
<html lang="en">
<head>
<meta charset="utf-8">
<title>Norvale Constructions – Business Cards</title>
<link href="https://fonts.googleapis.com/css2?family=Source+Sans+3:wght@400;600;700&display=swap" rel="stylesheet">
<style>
  :root {
    --green: #8dc63f;
    --white: #ffffff;
    --black: #000000;
    --ink: #333333;
    --ink-light: #f2f2f2;
    --divider-light: #bdbdbd;
    --divider-dark: #6a6a6a;
    --backdrop: #e6e4e0;
  }
  * { margin: 0; padding: 0; box-sizing: border-box; }
  html, body { width: 1200px; height: 720px; overflow: hidden; }
  body {
    background: var(--backdrop);
    font-family: "Source Sans 3", "Myriad Pro", Arial, sans-serif;
    position: relative;
  }
  .card {
    position: absolute;
    width: 555px;
    height: 316px;
  }
  .card--front-light { left: 34px; top: 28px; background: var(--white); color: var(--ink); }
  .card--back-green  { left: 618px; top: 28px; background: var(--green); color: var(--white); }
  .card--front-dark  { left: 34px; top: 376px; background: var(--black); color: var(--ink-light); }
  .card--back-dark   { left: 618px; top: 376px; background: var(--black); color: var(--white); }

  .wordmark {
    position: absolute;
    text-align: center;
    font-weight: 700;
    line-height: 1;
    color: var(--green);
  }
  .wordmark__name { display: block; }
  .wordmark__sub { display: block; letter-spacing: 0.06em; }

  .card--front-light .wordmark,
  .card--front-dark .wordmark { left: 40px; width: 260px; top: 118px; }
  .card--front-light .wordmark__name,
  .card--front-dark .wordmark__name { font-size: 54px; }
  .card--front-light .wordmark__sub,
  .card--front-dark .wordmark__sub { font-size: 20px; margin-top: 6px; }

  .card--back-green .wordmark,
  .card--back-dark .wordmark { left: 0; width: 100%; top: 98px; }
  .card--back-green .wordmark { color: var(--white); }
  .card--back-green .wordmark__name,
  .card--back-dark .wordmark__name { font-size: 74px; }
  .card--back-green .wordmark__sub,
  .card--back-dark .wordmark__sub { font-size: 27px; margin-top: 8px; }

  .divider {
    position: absolute;
    left: 319px; top: 62px;
    width: 1px; height: 192px;
    background: var(--divider-light);
  }
  .card--front-dark .divider { background: var(--divider-dark); }

  .contact {
    position: absolute;
    left: 339px; top: 62px;
    font-size: 15.5px;
  }
  .contact__name {
    color: var(--green);
    font-weight: 700;
    font-size: 18.5px;
    margin-bottom: 16px;
  }
  .contact__list { list-style: none; }
  .contact__item {
    display: flex; align-items: center; gap: 6px;
    height: 23px;
  }
  .contact__item svg { width: 12px; height: 12px; flex: none; fill: var(--green); stroke: var(--green); }
  .contact__address { margin-top: 16px; line-height: 20px; }

  .website {
    position: absolute;
    left: 0; width: 100%;
    top: 276px;
    text-align: center;
    font-size: 19px;
    letter-spacing: 0.22em;
  }
</style>
</head>
<body>

  <section class="card card--front-light">
    <div class="wordmark"><span class="wordmark__name">NORVALE</span><span class="wordmark__sub">CONSTRUCTIONS</span></div>
    <div class="divider"></div>
    <div class="contact">
      <p class="contact__name">PERSONS NAME</p>
      <ul class="contact__list">
        <li class="contact__item"><svg viewBox="0 0 12 12"><circle cx="6" cy="6" r="5.3" fill="none" stroke-width="1.2"/><path d="M4 3.2l1 1-.6.8c.4.9 1 1.5 1.9 1.9l.8-.6 1 1-.8 1C5.3 8.2 3.8 6.7 3 4z" stroke="none"/></svg>0987 654321</li>
        <li class="contact__item"><svg viewBox="0 0 12 12"><rect x="3" y="0.5" width="6" height="11" rx="1" stroke="none"/><rect x="4" y="2" width="4" height="4" fill="#fff" stroke="none"/></svg>0987 654321</li>
        <li class="contact__item"><svg viewBox="0 0 12 12"><path d="M1 5l5-3.5L11 5v5.5H1z" stroke="none"/><path d="M1.5 5.5L6 8.5l4.5-3" fill="none" stroke="#fff" stroke-width="1"/></svg>info@norvale.com</li>
        <li class="contact__item"><svg viewBox="0 0 12 12" fill="none"><circle cx="6" cy="6" r="5.2" fill="none" stroke-width="1"/><path d="M1 6h10M6 1v10M2.5 3.5h7M2.5 8.5h7" fill="none" stroke-width="0.8"/></svg>www.norvale.com</li>
      </ul>
      <p class="contact__address">00, Complex name<br>City, State 0042</p>
    </div>
  </section>

  <section class="card card--back-green">
    <div class="wordmark"><span class="wordmark__name">NORVALE</span><span class="wordmark__sub">CONSTRUCTIONS</span></div>
    <p class="website">www.norvale.com</p>
  </section>

  <section class="card card--front-dark">
    <div class="wordmark"><span class="wordmark__name">NORVALE</span><span class="wordmark__sub">CONSTRUCTIONS</span></div>
    <div class="divider"></div>
    <div class="contact">
      <p class="contact__name">PERSONS NAME</p>
      <ul class="contact__list">
        <li class="contact__item"><svg viewBox="0 0 12 12"><circle cx="6" cy="6" r="5.3" fill="none" stroke-width="1.2"/><path d="M4 3.2l1 1-.6.8c.4.9 1 1.5 1.9 1.9l.8-.6 1 1-.8 1C5.3 8.2 3.8 6.7 3 4z" stroke="none"/></svg>0987 654321</li>
        <li class="contact__item"><svg viewBox="0 0 12 12"><rect x="3" y="0.5" width="6" height="11" rx="1" stroke="none"/><rect x="4" y="2" width="4" height="4" fill="#000" stroke="none"/></svg>0987 654321</li>
        <li class="contact__item"><svg viewBox="0 0 12 12"><path d="M1 5l5-3.5L11 5v5.5H1z" stroke="none"/><path d="M1.5 5.5L6 8.5l4.5-3" fill="none" stroke="#000" stroke-width="1"/></svg>info@norvale.com</li>
        <li class="contact__item"><svg viewBox="0 0 12 12" fill="none"><circle cx="6" cy="6" r="5.2" fill="none" stroke-width="1"/><path d="M1 6h10M6 1v10M2.5 3.5h7M2.5 8.5h7" fill="none" stroke-width="0.8"/></svg>www.norvale.com</li>
      </ul>
      <p class="contact__address">00, Complex name<br>City, State 0042</p>
    </div>
  </section>

  <section class="card card--back-dark">
    <div class="wordmark"><span class="wordmark__name">NORVALE</span><span class="wordmark__sub">CONSTRUCTIONS</span></div>
    <p class="website">www.norvale.com</p>
  </section>

</body>
</html>
```